Letterhead for Conveyancing Company

Use existing logo to create a letterhead for a conveyancing company. Must be able to be used in Microsoft Word. Easy to read and professional.
Contact information to be at the bottom.
Bright Oak Conveyancing Pty Ltd
ACN 621 984 736PO Box 535 Campbelltown SA 5074
Mobile - 0461739286
Web address - www.brightoakconveyancing.com.au

Requirements
Must have
• Logo and contact details.
• Simple and professional.

```html
<!DOCTYPE html>
<html lang="en">
<head>
<meta charset="utf-8">
<title>Bright Oak Conveyancing Letterhead</title>
<link rel="stylesheet" href="https://fonts.googleapis.com/css2?family=Arimo:wght@400;700&display=swap">
<style>
  :root {
    --backdrop: #d9dcdd;
    --paper: #ffffff;
    --brand-pink: #e6379a;
    --soft-pink: #fbe3ef;
    --mid-pink: #f3bcd8;
    --text-grey: #555a5e;
  }
  * { box-sizing: border-box; margin: 0; padding: 0; }
  html, body { width: 1200px; height: 784px; overflow: hidden; }
  body {
    background: var(--backdrop);
    font-family: "Arimo", Arial, sans-serif;
    color: var(--text-grey);
  }
  .letterhead {
    position: absolute;
    left: 328px; top: 10px;
    width: 544px; height: 764px;
    background: var(--paper);
    box-shadow: 0 4px 14px rgba(0,0,0,.12);
    overflow: hidden;
  }
  .brand {
    position: absolute; left: 46px; top: 40px;
    display: flex; align-items: center; gap: 8px;
  }
  .brand-dot { width: 14px; height: 14px; border-radius: 50%; background: var(--brand-pink); }
  .brand-name { font-size: 26px; font-weight: 700; color: var(--brand-pink); letter-spacing: -0.5px; }
  .letter-body {
    position: absolute; left: 46px; top: 100px; width: 452px;
    font-size: 8.8px; line-height: 1.5;
  }
  .letter-body p { margin-bottom: 11px; }
  .signature {
    position: absolute; left: 46px; top: 420px;
    width: 150px; height: 38px;
    background: linear-gradient(90deg, #f1f1f2, #fafafa);
    border-radius: 4px;
  }
  .footer-band {
    position: absolute; left: 0; bottom: 0;
    width: 544px; height: 250px;
    background: linear-gradient(180deg, rgba(251,227,239,0) 0%, var(--soft-pink) 55%, var(--mid-pink) 100%);
  }
  .contact {
    position: absolute; left: 46px; right: 46px; bottom: 26px;
    list-style: none; font-size: 7.6px; line-height: 1.6;
    display: grid; grid-template-columns: 1fr 1fr; column-gap: 20px;
  }
  .contact li { display: flex; align-items: center; gap: 5px; white-space: nowrap; }
  .contact .icon {
    width: 7px; height: 7px; border-radius: 50%;
    background: var(--brand-pink); flex: none;
  }
  .contact .address { color: var(--brand-pink); font-weight: 700; }
</style>
</head>
<body>
  <main class="letterhead">
    <header class="brand">
      <span class="brand-dot"></span>
      <span class="brand-name">Bright Oak</span>
    </header>

    <section class="letter-body">
      <p>Lorem Ipsum is simply dummy text of the printing and typesetting industry. Lorem Ipsum has been the industry's standard dummy text ever since the 1500s, when an unknown printer took a galley of type and scrambled it to make a type specimen book. It has survived not only five centuries, but also the leap into electronic typesetting, remaining essentially unchanged. It was popularised in the 1960s with the release of Typeline sheets containing Lorem Ipsum passages, and more recently with desktop publishing software like Quillset Layout including versions of Lorem Ipsum.</p>
      <p>It is a long established fact that a reader will be distracted by the readable content of a page when looking at its layout. The point of using Lorem Ipsum is that it has a more-or-less normal distribution of letters, as opposed to using 'Content here, content here', making it look like readable English. Many desktop publishing packages and web page editors now use Lorem Ipsum as their default model text, and a search for 'lorem ipsum' will uncover many web sites still in their infancy. Various versions have evolved over the years, sometimes by accident, sometimes on purpose (injected humour and the like).</p>
      <p>Contrary to popular belief, Lorem Ipsum is not simply random text. It has roots in a piece of classical Latin literature from 45 BC, making it over 2000 years old. Daniel Harrow, a Latin professor at Ellisford College in Virginia, looked up one of the more obscure Latin words, consectetur, from a Lorem Ipsum passage, and going through the cites of the word in classical literature, discovered the undoubtable source. Lorem Ipsum comes from sections 1.10.32 and 1.10.33 of "de Finibus Bonorum et Malorum" structures, to generate Lorem Ipsum which looks reasonable. The generated Lorem Ipsum is therefore always free from repetition, injected humour, or non-characteristic words etc.</p>
    </section>

    <div class="signature" role="img" aria-label="Handwritten signature"></div>

    <div class="footer-band" role="img" aria-label="Soft pink and grey decorative swoosh along the lower edge"></div>

    <ul class="contact">
      <li class="address"><span class="icon"></span>PO Box 871 Marlowdale SA 5096</li>
      <li><span class="icon"></span>contact@brightoakconveyancing.com.au</li>
      <li><span class="icon"></span>ACN 583 217 469</li>
      <li><span class="icon"></span>www.brightoakconveyancing.com.au</li>
      <li><span class="icon"></span>0461739286</li>
    </ul>
  </main>
</body>
</html>
```